International Clinical Software Company needs a new business card design

We are looking for a new business card design for our company that has recently expanded into the UK market, making us a multinational company.
After having rebranded our website and produced a new style guide, we are looking for a business card that is creative and attention grabbing, while being consistent with the style and colour scheme used on the new website, www.plumvora.example
We produce care management technology for the aged care market, but the main aspect we aim to communicate is the human element of our software, and the way it assists in providing better care for aged people, and stronger relationships between aged people and the staff that care for them.
Our current business card is a dark green with gold text, which makes the text quite difficult to read, not very aesthetically appealing and the colour scheme looks quite dated.
We would like something fresh and modern, that can still be colourful but doesn't use large blocks of dark colour, and uses the colours within our logo.
Something tying in with the leaves that are used in our logo could work quite nicely, along with the Autumn/Fall colours of soft greens, yellows and reds (also in our existing logo). However also happy to look at fresh, completely out of the box ideas we may not have yet considered.
Target Market(s)
The people that receive this business card work in the aged card or health industry and are either corporate/management level staff or clinical (Registered Nurses, care workers etc.)
Industry/Entity Type
Health Product
Contact Information for Business Card
Company Name - BrindlewayCare
Company locations: United Kingdom, Australia, New Zealand
Staff Details:
Staff name: Derek Mallow
Staff job title: Executive Chairman
Staff email: d.mallow@plumvora.example
Office phone number: 01742 918576
Font styles to use
Other font styles liked:
- Calibri
Requirements
Must have
- Must include the BrindlewayCare brand name in it's current font
- Must include logo (3 leaves in gold circle)
- Must include Business Card Details
Nice to have
- Elements of gold
- White space
- Something autumn themed but not too cliched
Should not have
- No blue - used by a major competitor and we would like to differentiate from them
- Large blocks of dark green colour (the green that appears in our leaves on the logo on our current business card is the background colour and it is far too dark)

```html
<!DOCTYPE html>
<html lang="en">
<head>
<meta charset="utf-8">
<title>BrindlewayCare Business Card</title>
<link href="https://fonts.googleapis.com/css2?family=Open+Sans:wght@300;400;600;700&display=swap" rel="stylesheet">
<style>
  :root {
    --backdrop-top: #2a2a2a;
    --backdrop-bottom: #050505;
    --card-white: #ffffff;
    --gold: #b09a6b;
    --gold-deep: #a3834d;
    --gold-line: #8a7447;
    --text-grey: #5b5b5b;
  }
  * { margin: 0; padding: 0; box-sizing: border-box; }
  html, body {
    width: 1200px;
    height: 900px;
    overflow: hidden;
  }
  body {
    position: relative;
    background: linear-gradient(180deg, var(--backdrop-top) 0%, #1a1a1a 55%, var(--backdrop-bottom) 100%);
    font-family: "Open Sans", Arial, sans-serif;
  }
  .card {
    position: absolute;
    top: 170px;
    width: 347px;
    height: 561px;
    box-shadow: 0 4px 14px rgba(0,0,0,0.45);
  }
  .card-front {
    left: 259px;
    background: var(--card-white);
  }
  .card-back {
    left: 631px;
    background: var(--gold);
  }
  .gold-tab {
    position: absolute;
    left: 102px;
    width: 143px;
    background: var(--gold);
  }
  .gold-tab--top { top: 0; height: 30px; }
  .gold-tab--bottom { bottom: 0; height: 28px; }
  .brand-mark {
    position: absolute;
    top: 104px;
    left: 0;
    width: 100%;
    display: flex;
    flex-direction: column;
    align-items: center;
  }
  .brand-circle {
    width: 96px;
    height: 96px;
    border: 3px solid var(--gold);
    border-radius: 50%;
  }
  .brand-name {
    margin-top: 22px;
    font-weight: 300;
    font-size: 36px;
    line-height: 1;
    color: var(--gold);
    letter-spacing: 0.5px;
  }
  .contact {
    position: absolute;
    top: 328px;
    left: 0;
    width: 100%;
    text-align: center;
    color: var(--text-grey);
    font-size: 15px;
    line-height: 20px;
  }
  .contact-name {
    font-weight: 700;
    font-size: 18px;
    color: var(--gold-deep);
    line-height: 22px;
  }
  .contact-email {
    margin-top: 15px;
    display: flex;
    justify-content: center;
    align-items: center;
    gap: 4px;
  }
  .contact-email svg { width: 11px; height: 11px; }
  .contact-locations { margin-top: 16px; }
  .back-emblem {
    position: absolute;
    left: 30px;
    top: 137px;
    width: 287px;
    height: 287px;
    border: 2px solid var(--gold-line);
    border-radius: 50%;
    display: flex;
    align-items: center;
    justify-content: center;
  }
  .back-name {
    font-weight: 300;
    font-size: 30px;
    color: var(--card-white);
    letter-spacing: 0.5px;
  }
</style>
</head>
<body>
  <section class="card card-front" aria-label="Business card front">
    <div class="gold-tab gold-tab--top"></div>
    <div class="brand-mark">
      <div class="brand-circle"></div>
      <div class="brand-name">BrindlewayCare</div>
    </div>
    <div class="contact">
      <p class="contact-name">Derek Mallow</p>
      <p class="contact-title">Executive Chairman</p>
      <p class="contact-email">
        <svg viewBox="0 0 24 24" aria-hidden="true"><path fill="#b09a6b" d="M6.6 10.8a15.1 15.1 0 0 0 6.6 6.6l2.2-2.2c.3-.3.7-.4 1-.2 1.1.4 2.3.6 3.6.6.6 0 1 .4 1 1V20c0 .6-.4 1-1 1A17 17 0 0 1 3 4c0-.6.4-1 1-1h3.5c.6 0 1 .4 1 1 0 1.3.2 2.5.6 3.6.1.3 0 .7-.2 1z"/></svg>
        d.mallow@plumvora.example
      </p>
      <p class="contact-locations">United Kingdom, Australia<br>New Zealand</p>
    </div>
    <div class="gold-tab gold-tab--bottom"></div>
  </section>

  <section class="card card-back" aria-label="Business card back">
    <div class="back-emblem">
      <span class="back-name">BrindlewayCare</span>
    </div>
  </section>
</body>
</html>
```